V.Lumo Gin - Bottle label Design

We are manufacturers of Gin in South Africa.
The name of our Gin is V.Lumo Gin with Q standing for Dlovikazi, a Xhosa Village in the region of Eastern Cape.

We would like our brand to depict the following (really the focus of Gold on it)
> Prosperity of the place
> Wealth of the place, land, material or in the people
> Gold rush, potential, hope

As the brand matures, we would like to have campaigns with it. See ideas below:
> V.Lumo Premium
> Crimson dusk edition
Limited edition will be released every year
- V.Lumo entabeni (location)
- V.Lumo ekhayeni (location)

> Each batch of bottles with focus on a specific area/location in Dlovikazi. One that is known and will be highlighted on the map design of the bottle.
Bottles based on landmarks in Dlovikazi and landmark design in the Big V.

Below we tried but we are not where we really want to be in terms of Gin Bottle elegance.

Target Market(s)

Target market is the young crowd. Young Xhosa men and women working really hard to get their goals. Positive thinkers. Elegant. Fresh. Bold. Age from 24 to 45. People who enjoy quality products.

Industry/Entity Type

Beverage Industry. Craft Gin.

Font styles to use
Sans Serif
Decorative

Colors
FFF300
FFF600
FEFA6F
FFFEC7
FFFEE8
FFC000
F8CF3A
FAE287
FDF2CF
FEFAEE

Requirements
Must have
• Gold colour as a theme. Try and make the background textured.

```html
<!DOCTYPE html>
<html lang="en">
<head>
<meta charset="utf-8">
<title>V.Lumo Gin – Bottle Label</title>
<link rel="stylesheet" href="https://fonts.googleapis.com/css2?family=Montserrat:wght@500;800&family=Roboto+Condensed:wght@400;500&family=Roboto:wght@400;500&display=swap">
<style>
  :root {
    --gold-deep: #9a7414;
    --gold-mid: #c9a227;
    --gold-bright: #f8cf3a;
    --gold-light: #fae287;
    --gold-pale: #fdf2cf;
    --cream: #fefaee;
    --paper: #fbfbf8;
    --ink: #161616;
    --ink-soft: #2b2412;
    --stage: #ffffff;
  }
  * { box-sizing: border-box; margin: 0; padding: 0; }
  html, body {
    width: 1200px; height: 1200px; overflow: hidden;
    background: var(--stage);
  }
  .canvas { position: relative; width: 1200px; height: 1200px; }

  .label {
    position: absolute; left: 150px; top: 142px;
    width: 900px; height: 915px;
    background:
      repeating-linear-gradient(180deg, transparent 0 6px, rgba(190,160,70,0.16) 6px 7px),
      var(--paper);
    border-left: 3px solid var(--gold-mid);
    border-right: 3px solid var(--gold-mid);
    box-shadow: 0 0 0 1px rgba(150,120,40,0.25);
  }
  .label__band {
    position: absolute; left: 0; right: 0;
    background: linear-gradient(90deg, var(--gold-deep), var(--gold-bright) 30%, var(--gold-light) 50%, var(--gold-bright) 70%, var(--gold-deep));
  }
  .label__band--top { top: 0; height: 12px; }
  .label__band--bottom { bottom: 10px; height: 18px; border-top: 3px solid var(--paper); }

  .label__landscape {
    position: absolute; left: 15px; right: 15px; top: 24px; height: 410px;
    background:
      radial-gradient(ellipse 60% 38% at 55% 38%, rgba(201,162,39,0.75), rgba(248,207,58,0.35) 55%, transparent 75%),
      radial-gradient(ellipse 70% 30% at 45% 72%, rgba(250,226,135,0.7), transparent 80%);
  }

  .brand {
    position: absolute; left: 0; right: 0; top: 425px;
    display: flex; justify-content: center; align-items: center; gap: 22px;
  }
  .brand__mark {
    width: 90px; height: 90px; border-radius: 50%;
    background: linear-gradient(135deg, var(--gold-bright), var(--gold-deep));
  }
  .brand__name {
    font-family: "Montserrat", sans-serif; font-weight: 800;
    font-size: 124px; line-height: 1; letter-spacing: -2px;
    color: var(--ink);
  }

  .product {
    position: absolute; left: 0; right: 0; top: 604px;
    text-align: center;
    font-family: "Roboto", sans-serif; font-weight: 500;
    font-size: 104px; line-height: 1; color: var(--ink-soft);
  }

  .facts {
    position: absolute; left: 141px; top: 747px; width: 623px; height: 123px;
    background: linear-gradient(90deg, #b88d1f, var(--gold-light) 45%, var(--gold-bright) 65%, #a67d1a);
    border: 2px solid #4d3a0c;
    padding: 5px;
  }
  .facts__grid {
    width: 100%; height: 100%;
    border: 2px solid #4d3a0c;
    display: grid;
    grid-template-columns: 1fr 168px;
    grid-template-rows: 1fr 1fr;
  }
  .facts__cell {
    display: flex; align-items: center; justify-content: center;
    color: var(--ink-soft); text-align: center;
  }
  .facts__cell--left { border-right: 2px solid #4d3a0c; }
  .facts__cell--top { border-bottom: 2px solid #4d3a0c; }
  .facts__story {
    font-family: "Roboto", sans-serif; font-size: 16px; line-height: 1.05;
    text-transform: uppercase;
  }
  .facts__abv, .facts__volume {
    font-family: "Roboto", sans-serif; font-weight: 500; font-size: 24px;
  }
  .facts__origin {
    font-family: "Roboto Condensed", sans-serif; font-weight: 500;
    font-size: 28px; letter-spacing: 2px; text-transform: uppercase;
  }
</style>
</head>
<body>
<main class="canvas">
  <section class="label">
    <div class="label__band label__band--top"></div>

    <div class="label__landscape" role="img" aria-label="Gold foil engraving of a hilltop village landscape in the Dlovikazi region"></div>

    <div class="brand">
      <span class="brand__mark"></span>
      <span class="brand__name">V.Lumo</span>
    </div>

    <h1 class="product">GIN</h1>

    <div class="facts">
      <div class="facts__grid">
        <div class="facts__cell facts__cell--left facts__cell--top">
          <p class="facts__story">Triple distilled with the rich &amp;<br>aromatic taste of the Dlovikazi region</p>
        </div>
        <div class="facts__cell facts__cell--top">
          <p class="facts__abv">40% alc.vol.</p>
        </div>
        <div class="facts__cell facts__cell--left">
          <p class="facts__origin">Made in Eastern Cape</p>
        </div>
        <div class="facts__cell">
          <p class="facts__volume">700 ml</p>
        </div>
      </div>
    </div>

    <div class="label__band label__band--bottom"></div>
  </section>
</main>
</body>
</html>
```